Recruitment of Trellan Staffing for the UK market

I want a website for the UK market to attract businesses and companies to come to us for Philipine labour. We want an information site that gives all information on what we do and how we can recruit Philippine labour.
This is a recruitment site for companies to contact us with their requirements for skilled workers coming from the Philipines over to the UK to work.

Target Market(s)

Uk Companies and businesses who want Philipine skilled workers

Industry/Entity Type

REcruitment

Coding

Number of Pages Required

5+ page

Font styles to use
Sans Serif

Colors
0054AA
0677BA
7BADD7
CADEEF
E8F1F8
0094D4
00A9DD
6FCCEA
C7EBF8
E9F6FB
EE7325
F08F49
F5BC92
FAE3D3
FDF4ED
EB3D1F
EC4F4E
F09395
F8D3D4
FCEDEE

Requirements
Must have
• Look professional and corperate with drop down menus for Home ,about, services,articles. training , contact us
Nice to have
• Look at Velmora recruitment- https://velmorarecruitment.example.co.uk/. This is my current site - https://www.trellanstaffing.example.com/
Should not have
• Cartoons or silly pictures , needs to be corperate looking

```html
<!DOCTYPE html>
<html lang="en">
<head>
<meta charset="utf-8">
<title>Trellan Staffing – Skilled Philippine Workers for UK Companies</title>
<link href="https://fonts.googleapis.com/css2?family=Roboto:wght@400;500;700;900&display=swap" rel="stylesheet">
<style>
:root{
  --red:#EC4F4E;
  --pink:#F8D3D4;
  --ink:#1f1f1f;
  --text:#555;
  --grey-bg:#f2f2f2;
  --line:#e2e2e2;
  --white:#fff;
}
*{box-sizing:border-box;margin:0;padding:0}
html,body{width:1200px;height:3468px;overflow:hidden}
body{position:relative;font-family:"Roboto",Arial,sans-serif;color:var(--ink);background:var(--white)}
.abs{position:absolute}
a{color:inherit;text-decoration:none}
p{font-size:14px;line-height:1.6;color:var(--text)}
.btn{display:inline-block;background:var(--red);color:#fff;font-weight:700;font-size:13px;letter-spacing:.5px;padding:13px 24px;border-radius:4px}
.link-more{color:var(--red);font-weight:700;font-size:13px;letter-spacing:.5px}

/* Header */
.site-header{left:0;top:0;width:1200px;height:112px;background:#fff;display:flex;align-items:center;justify-content:space-between;padding:0 112px}
.brand{display:flex;align-items:center;gap:10px;font-weight:900;font-size:24px;color:var(--red)}
.brand-dot{width:22px;height:22px;background:var(--red);border-radius:50%}
.main-nav{display:flex;gap:34px;font-size:15px;font-weight:500}

/* Hero */
.hero{left:0;top:112px;width:1200px;height:448px;background:linear-gradient(90deg,#ededed,#f6f6f6 60%,#ececec)}
.hero-title{left:112px;top:64px;width:500px;font-size:42px;line-height:1.25;font-weight:900;text-transform:uppercase}
.hero .btn{left:112px;top:340px}
.about-title{left:640px;top:66px;font-size:27px;font-weight:700}
.about-text{left:640px;top:122px;width:450px}
.about-photos{left:640px;top:296px;display:flex;gap:8px}
.about-photos div{width:106px;height:106px;border-radius:4px}

/* Working together */
.section-title{font-size:30px;font-weight:900;text-align:center;width:1200px;left:0}
.wt-title{top:680px}
.wt-sub{top:736px;left:300px;width:600px;text-align:center}
.step{width:222px;height:216px;top:912px;background:var(--red);color:#fff;padding:22px}
.step-num{width:48px;height:48px;border-radius:50%;background:#fff;color:var(--red);display:flex;align-items:center;justify-content:center;font-weight:700;font-size:18px}
.step-label{position:absolute;left:22px;bottom:22px;font-weight:700;font-size:17px}
.step-raised{top:826px;height:302px;background:#fff;box-shadow:0 8px 26px rgba(0,0,0,.14);color:var(--ink);text-align:center;padding:24px 22px}
.step-raised .step-num{margin:0 auto 26px;background:var(--pink);color:var(--red)}
.step-raised h3{font-size:17px;font-weight:900;margin-bottom:14px}
.step-raised p{font-size:13px;margin-bottom:12px}

/* Team photo */
.team-photo{left:0;top:1250px;width:1200px;height:640px;background:linear-gradient(180deg,#d9d6d2 0%,#bfb8b0 45%,#8f8a86 100%)}

/* Info card */
.info-card{left:80px;top:1600px;width:1008px;height:820px;background:#fff;border-radius:22px;box-shadow:0 10px 40px rgba(0,0,0,.12)}
.workers-title{left:64px;top:20px;width:340px;font-size:38px;line-height:1.15;font-weight:900}
.workers-text{left:64px;top:160px;width:340px;font-size:13px}
.url{color:var(--red);font-size:13px;line-height:1.5;word-break:break-all}
.workers-url{left:64px;top:420px;width:320px}
.info-card .workers-btn{left:64px;top:520px}
.card-h{font-size:28px;font-weight:900}
.sponsor-title{left:492px;top:112px}
.sponsor-text{left:492px;top:160px;width:470px;font-size:13px}
.sponsor-url{left:492px;top:290px;width:470px;font-size:13px}
.sponsor-more{left:492px;top:360px}
.timeline-title{left:492px;top:420px}
.timeline-text{left:492px;top:468px;width:470px;font-size:13px}
.tl-list{left:492px;top:520px;width:480px;list-style:none}
.tl-list li{display:flex;gap:10px;margin-bottom:14px;font-size:13px;line-height:1.6;color:var(--text)}
.tl-list svg{flex:none;margin-top:3px}
.timeline-more{left:492px;top:720px}

/* Contact */
.contact{left:0;top:2470px;width:1200px;height:520px;background:var(--grey-bg)}
.contact-title{top:100px}
.contact-item{left:112px;display:flex;gap:18px;align-items:flex-start}
.c-icon{width:42px;height:42px;border-radius:50%;background:var(--red);display:flex;align-items:center;justify-content:center;flex:none}
.contact-item h4{font-size:15px;font-weight:900;margin-bottom:4px}
.contact-item p{font-size:13px;line-height:1.5;color:var(--ink)}
.field{left:432px;width:308px;height:50px;background:#fff;border:1px solid var(--line);font-size:13px;color:#999;padding:16px}
.submit{left:432px;top:392px;width:308px;height:46px;background:var(--red);color:#fff;font-weight:700;font-size:13px;display:flex;align-items:center;justify-content:center}
.message{left:768px;top:176px;width:320px;height:284px;background:#fff;border:1px solid var(--line);font-size:13px;color:#999;padding:16px}

/* Footer */
.footer-h{font-size:14px;font-weight:900;text-transform:uppercase;top:3064px}
.footer-h::after{content:"";display:block;width:28px;height:2px;background:var(--red);margin-top:8px}
.map{left:112px;top:3114px;width:230px;height:170px;background:linear-gradient(135deg,#cfe2ee,#e6eef2 60%,#d8e7d2)}
.quick{left:392px;top:3112px;list-style:none}
.quick li{font-size:14px;margin-bottom:10px}
.fcontact{left:536px;top:3112px;width:240px;list-style:none}
.fcontact li{display:flex;gap:8px;font-size:13px;line-height:1.5;margin-bottom:10px}
.fcontact svg{flex:none;margin-top:3px}
.news-text{left:808px;top:3112px;width:280px;font-size:13px}
.news-form{left:808px;top:3180px;width:280px;height:44px;background:#f3f3f3;border-radius:22px;display:flex;align-items:center;justify-content:space-between;padding:0 4px 0 18px;font-size:13px;color:#999}
.news-go{width:36px;height:36px;border-radius:50%;background:var(--red);display:flex;align-items:center;justify-content:center}
.copyright{left:0;top:3400px;width:1200px;height:68px;text-align:center;font-size:13px;line-height:68px;border-top:1px solid var(--line)}
.copyright span{color:var(--red)}
</style>
</head>
<body>

<header class="site-header abs">
  <div class="brand"><span class="brand-dot"></span>Trellan Staffing</div>
  <nav class="main-nav">
    <a href="#">Home</a><a href="#">About</a><a href="#">Services</a><a href="#">Articles</a><a href="#">Training</a><a href="#">Contact Us</a>
  </nav>
</header>

<section class="hero abs">
  <h1 class="hero-title abs">Recruiting and<br>placing skilled<br>Philippine workers<br>into UK companies</h1>
  <a class="btn abs" href="#">LEARN MORE</a>
  <h2 class="about-title abs">WHAT THE BUSINESS IS ABOUT</h2>
  <p class="about-text abs">We source skilled workers directly from the Philippines to work in the UK. With offices, training locations and specialist recruiters we can find the highest quality individuals to add value and resources to any UK businesses. We deliver quality based on vast experience over a number of years.</p>
  <div class="about-photos abs">
    <div role="img" aria-label="Photo of a construction worker" style="background:linear-gradient(135deg,#8e8a84,#c9c2b8)"></div>
    <div role="img" aria-label="Photo of a care worker with a client" style="background:linear-gradient(135deg,#b7a79a,#e0d6cc)"></div>
    <div role="img" aria-label="Photo of a group of recruited workers" style="background:linear-gradient(135deg,#6c7a88,#a9b5bf)"></div>
    <div role="img" aria-label="Photo of healthcare staff in uniform" style="background:linear-gradient(135deg,#4c7fae,#9cc0de)"></div>
  </div>
</section>

<h2 class="section-title wt-title abs">WORKING TOGETHER</h2>
<p class="wt-sub abs">We recruit the finest talent available with our dedicated 200 strong team. Our services are highlighted in red dots on the map.</p>

<div class="step abs" style="left:112px"><div class="step-num">01</div><div class="step-label">WHAT WE DO</div></div>
<div class="step step-raised abs" style="left:358px">
  <div class="step-num">02</div>
  <h3>HOW WE HELP</h3>
  <p>We work with companies to find skilled workers that meet the UK requirements for Visas and work permits.</p>
  <a class="link-more" href="#">LEARN MORE</a>
</div>
<div class="step abs" style="left:608px"><div class="step-num">03</div><div class="step-label">WHERE TO START</div></div>
<div class="step abs" style="left:860px"><div class="step-num">04</div><div class="step-label">CONTACT US TODAY</div></div>

<div class="team-photo abs" role="img" aria-label="Photo of a professional recruitment team standing together in an office"></div>

<section class="info-card abs">
  <h2 class="workers-title abs">UK SKILLED WORKERS LIST</h2>
  <p class="workers-text abs">The UK government since Brexit have developed a new system based on points (similar to Australia) when recruiting from outside of the UK. Previously EU citizens could work in the UK without any extensive documentation or classification of skills. This has all changed. Overseas recruitment must now focus on skills that are currently short in the UK. The list is extensive and is constantly being reviewed. The list can be found here:</p>
  <a class="url workers-url abs" href="#">https://www.example.gov.uk/skilled-worker-visa-eligible-occupations</a>
  <a class="btn workers-btn abs" href="#">LEARN MORE</a>

  <h2 class="card-h sponsor-title abs">SPONSOR LICENCE</h2>
  <p class="sponsor-text abs">If you have areas of your business that meet the entry requirements of skilled labour your next step is to gain a sponsor licence for your business. There are different types of licences depending on the size of the business.</p>
  <p class="sponsor-url abs">All information can be found here:<br><a class="url" href="#">https://www.example.gov.uk/apply-sponsor-licence</a></p>
  <a class="link-more sponsor-more abs" href="#">LEARN MORE</a>

  <h2 class="card-h timeline-title abs">RECRUITMENT TIMELINE</h2>
  <p class="timeline-text abs">Brief us on the job profiles – this is passed on to our teams in the Philippines.</p>
  <ul class="tl-list abs">
    <li><svg width="14" height="14" viewBox="0 0 14 14"><circle cx="7" cy="7" r="7" fill="#EC4F4E"/><path d="M4 7l2 2 4-4" stroke="#fff" stroke-width="1.6" fill="none"/></svg>Our teams in the Philippines source suitable candidates, documentation required for each candidate will be checked and vetted by the Recruitment Team. Once deemed qualified, they will now be assessed by their Technical Interviewer.</li>
    <li><svg width="14" height="14" viewBox="0 0 14 14"><circle cx="7" cy="7" r="7" fill="#EC4F4E"/><path d="M4 7l2 2 4-4" stroke="#fff" stroke-width="1.6" fill="none"/></svg>The candidates must provide a police check as pre-requisite for recruitment process to proceed.</li>
  </ul>
  <a class="link-more timeline-more abs" href="#">LEARN MORE</a>
</section>

<section class="contact abs">
  <h2 class="section-title contact-title abs">CONTACT US</h2>
  <div class="contact-item abs" style="top:172px">
    <span class="c-icon"><svg width="18" height="18" viewBox="0 0 24 24"><path d="M12 2a7 7 0 0 0-7 7c0 5 7 13 7 13s7-8 7-13a7 7 0 0 0-7-7zm0 9.5A2.5 2.5 0 1 1 12 6.5a2.5 2.5 0 0 1 0 5z" fill="#fff"/></svg></span>
    <div><h4>LOCATION</h4><p>Elmstead Gardens, Marrowfield<br>Marrowfield MF1 2ZZ United Kingdom</p></div>
  </div>
  <div class="contact-item abs" style="top:292px">
    <span class="c-icon"><svg width="18" height="18" viewBox="0 0 24 24"><path d="M6.6 10.8a15 15 0 0 0 6.6 6.6l2.2-2.2a1 1 0 0 1 1-.25 11.4 11.4 0 0 0 3.6.57 1 1 0 0 1 1 1V20a1 1 0 0 1-1 1A17 17 0 0 1 3 4a1 1 0 0 1 1-1h3.5a1 1 0 0 1 1 1c0 1.25.2 2.45.57 3.57a1 1 0 0 1-.25 1z" fill="#fff"/></svg></span>
    <div><h4>PHONE</h4><p>07700 900481</p></div>
  </div>
  <div class="contact-item abs" style="top:386px">
    <span class="c-icon"><svg width="18" height="18" viewBox="0 0 24 24"><path d="M3 5h18v14H3z" fill="#fff"/><path d="M3 5l9 7 9-7" stroke="#EC4F4E" stroke-width="1.6" fill="none"/></svg></span>
    <div><h4>EMAIL</h4><p>sales@trellanstaffing.example.com</p></div>
  </div>
  <div class="field abs" style="top:176px">Name</div>
  <div class="field abs" style="top:246px">Phone</div>
  <div class="field abs" style="top:316px">Email</div>
  <div class="submit abs">SUBMIT</div>
  <div class="message abs">Type your message</div>
</section>

<h3 class="footer-h abs" style="left:112px">Find Us</h3>
<div class="map abs" role="img" aria-label="Map showing the office location in the Philippines"></div>

<h3 class="footer-h abs" style="left:392px">Quick Links</h3>
<ul class="quick abs"><li>Home</li><li>About</li><li>Services</li><li>Articles</li><li>Training</li><li>Contact Us</li></ul>

<h3 class="footer-h abs" style="left:536px">Contact Details</h3>
<ul class="fcontact abs">
  <li><svg width="12" height="14" viewBox="0 0 24 24"><path d="M12 2a7 7 0 0 0-7 7c0 5 7 13 7 13s7-8 7-13a7 7 0 0 0-7-7z" fill="#EC4F4E"/></svg>Elmstead Gardens, Marrowfield Marrowfield MF1 2ZZ United Kingdom</li>
  <li><svg width="12" height="14" viewBox="0 0 24 24"><path d="M3 5h18v14H3z" fill="#EC4F4E"/></svg>sales@trellanstaffing.example.com</li>
  <li><svg width="12" height="14" viewBox="0 0 24 24"><circle cx="12" cy="12" r="9" fill="#EC4F4E"/></svg>07700 900481</li>
</ul>

<h3 class="footer-h abs" style="left:808px">Subscribe to our Newsletter</h3>
<p class="news-text abs">Join our mailing list for news, updates and guidance on recruiting.</p>
<div class="news-form abs">Enter Your Email<span class="news-go"><svg width="14" height="14" viewBox="0 0 24 24"><path d="M2 21l21-9L2 3v7l15 2-15 2z" fill="#fff"/></svg></span></div>

<footer class="copyright abs">©Copyrights 2023 <span>Trellan Staffing Ltd</span> | All Rights Reserved</footer>

</body>
</html>
```